Meridale Bed Company Needs Business Card

Looking for a very nice looking business card. Creative but not extravagant. We sell beds and pillows across the U.S. and need something professional but catchy. I have attached the logo.

Name : Devin Holt
Title : President
Phone : (800) 471-2960
Email: sleep@quilmora.com
Website: www.quilmora.com

Can be single-sided or double-sided
horizontal or vertical

Can use Blues/Greys

Target Market(s)

Mass Market

Industry/Entity Type

Retail

Contact Information for Business Card

Name : Devin Holt
Title : President
Phone : (800) 471-2960
Email: sleep@quilmora.com
Website: www.quilmora.com

Requirements
Must have
• Clean, Modern, Smooth
• Can use Blues/Greys
• On the other side without the information - have something simple like www.quilmora.com or our logo
Nice to have
• Surprise me
Should not have
• Nothing crazy, nothing cluttered

```html
<!DOCTYPE html>
<html lang="en">
<head>
<meta charset="utf-8">
<title>Meridale Bed Company – Business Card</title>
<link rel="stylesheet" href="https://fonts.googleapis.com/css2?family=Source+Sans+3:wght@400;600&display=swap">
<style>
  :root {
    --stage: #000000;
    --card: #2f3034;
    --accent: #2f9fd8;
    --ink: #f2f2f2;
  }
  html, body {
    margin: 0;
    padding: 0;
    width: 1200px;
    height: 900px;
    overflow: hidden;
    background: var(--stage);
    font-family: "Source Sans 3", "Myriad Pro", Arial, sans-serif;
  }
  .canvas {
    position: relative;
    width: 1200px;
    height: 900px;
  }
  .card {
    position: absolute;
    top: 271px;
    width: 457px;
    height: 281px;
    border-radius: 14px;
    background: var(--card);
    text-align: center;
  }
  .card--front { left: 137px; }
  .card--back { left: 626px; }

  .contact-name {
    position: absolute;
    top: 66px;
    left: 0;
    right: 0;
    margin: 0;
    font-size: 20px;
    font-weight: 600;
    color: var(--accent);
    line-height: 24px;
  }
  .contact-title {
    position: absolute;
    top: 86px;
    left: 0;
    right: 0;
    margin: 0;
    font-size: 14.5px;
    font-weight: 400;
    color: var(--ink);
    line-height: 18px;
  }
  .divider {
    position: absolute;
    top: 127px;
    left: 179px;
    width: 100px;
    height: 2px;
  }
  .contact-list {
    position: absolute;
    top: 151px;
    left: 0;
    right: 0;
    margin: 0;
    padding: 0;
    list-style: none;
    font-size: 13.5px;
    color: var(--ink);
    line-height: 19px;
  }

  .brand-name {
    position: absolute;
    top: 84px;
    left: 0;
    right: 0;
    margin: 0;
    font-size: 80px;
    font-weight: 400;
    letter-spacing: 1px;
    color: var(--accent);
    line-height: 96px;
  }
  .brand-url {
    position: absolute;
    top: 208px;
    left: 0;
    right: 0;
    margin: 0;
    font-size: 13.5px;
    font-weight: 600;
    color: var(--accent);
    line-height: 18px;
  }
</style>
</head>
<body>
  <main class="canvas">
    <section class="card card--front" aria-label="Business card, contact side">
      <h1 class="contact-name">Devin Holt</h1>
      <p class="contact-title">President</p>
      <svg class="divider" viewBox="0 0 100 2" aria-hidden="true">
        <line x1="0" y1="1" x2="100" y2="1" stroke="var(--accent)" stroke-width="1" stroke-dasharray="2.5 1.5"/>
      </svg>
      <ul class="contact-list">
        <li>(800) 471-2960</li>
        <li>sleep@quilmora.com</li>
        <li>www.quilmora.com</li>
      </ul>
    </section>

    <section class="card card--back" aria-label="Business card, brand side">
      <p class="brand-name">quilmora</p>
      <p class="brand-url">www.quilmora.com</p>
    </section>
  </main>
</body>
</html>
```